Local fast-growing company in the service sector

We are looking for a modern business card design, which should also appear on our letterheads

Target Market(s)

Private and industrial sectors

Contact Information for Business Card

Vorname Name
Kellberger Str. 18
73548 Lindenau
Tel.: 07146-839214-0
Name@agentur-kvtl.de

Colors
9d9d9d
919191
aaaaaa

Requirements
Must have
• The logo (file) in silver

```html
<!DOCTYPE html>
<html lang="de">
<head>
<meta charset="utf-8">
<title>KVTL Visitenkarte</title>
<link href="https://fonts.googleapis.com/css2?family=Montserrat:wght@400;500;700;800&display=swap" rel="stylesheet">
<style>
  :root {
    --backdrop: #4a4a4a;
    --card: #2a2a2b;
    --card-edge: #333334;
    --silver: #aaaaaa;
    --silver-mid: #9d9d9d;
    --silver-dark: #919191;
    --text-light: #e6e6e6;
  }
  * { margin: 0; padding: 0; box-sizing: border-box; }
  html, body {
    width: 799px; height: 1200px; overflow: hidden;
    background: var(--backdrop);
    font-family: "Montserrat", sans-serif;
  }
  .canvas {
    position: relative; width: 799px; height: 1200px;
    background: radial-gradient(ellipse at 60% 40%, #5c5c5c 0%, var(--backdrop) 70%);
  }
  .card {
    position: absolute; left: 110px; width: 580px; height: 330px;
    background: radial-gradient(ellipse at 55% 45%, #3a3a3b 0%, var(--card) 75%);
    border: 1px solid var(--card-edge);
    box-shadow: 0 14px 30px rgba(0,0,0,0.45);
  }
  .card--front { top: 120px; }
  .card--back { top: 740px; }

  .wordmark {
    display: flex; align-items: center; gap: 16px;
    font-weight: 800; color: var(--silver); letter-spacing: 2px;
    white-space: nowrap;
  }
  .wordmark__square { background: var(--silver-dark); }
  .card--front .wordmark {
    position: absolute; left: 50%; top: 50%;
    transform: translate(-50%, -50%);
    font-size: 84px;
  }
  .card--front .wordmark__square { width: 70px; height: 70px; }

  .card--back .wordmark {
    position: absolute; right: 36px; bottom: 64px;
    font-size: 52px; gap: 12px;
  }
  .card--back .wordmark__square { width: 44px; height: 44px; }

  .holder-name {
    position: absolute; left: 36px; top: 40px;
    font-size: 15px; font-weight: 800; letter-spacing: 2.5px;
    color: var(--silver-mid); text-transform: uppercase;
    white-space: nowrap;
  }
  .contact {
    position: absolute; left: 36px; bottom: 40px;
    list-style: none; color: var(--text-light);
    font-size: 13px; font-weight: 500; letter-spacing: 0.6px;
    white-space: nowrap;
  }
  .contact li { display: flex; align-items: center; gap: 8px; line-height: 1.65; }
  .contact svg { width: 11px; height: 11px; fill: none; stroke: var(--text-light); stroke-width: 1.6; }
</style>
</head>
<body>
<main class="canvas">
  <section class="card card--front" aria-label="Vorderseite">
    <div class="wordmark"><span class="wordmark__square"></span>KVTL</div>
  </section>

  <section class="card card--back" aria-label="Rückseite">
    <p class="holder-name">Vorname Name</p>
    <ul class="contact">
      <li>
        <svg viewBox="0 0 12 12"><path d="M3 1 L5 3.5 L4 5 Q5 7 7 8 L8.5 7 L11 9 L9.5 11 Q2 10 1 2.5 Z"/></svg>
        07146-839214-0
      </li>
      <li>
        <svg viewBox="0 0 12 12"><rect x="1" y="2.5" width="10" height="7"/><path d="M1 2.5 L6 6.5 L11 2.5"/></svg>
        Name@agentur-kvtl.de
      </li>
      <li>
        <svg viewBox="0 0 12 12"><circle cx="6" cy="6" r="5"/><ellipse cx="6" cy="6" rx="2.2" ry="5"/><path d="M1 6 H11"/></svg>
        www.agentur-kvtl.de
      </li>
      <li class="contact__address">Kellberger Str. 18 73548 Lindenau</li>
    </ul>
    <div class="wordmark"><span class="wordmark__square"></span>KVTL</div>
  </section>
</main>
</body>
</html>
```